Computer consultant business card

Bexil Software is a newly started computer consulting company. It's a small one-man company that provides mostly Vornix applications but also websites in collaboration with designers. I'm running this company on the side of full time university studies.

I want the final design to be clean and memorable. Be creative! :)

Some inspiration:
http://www.pixelmarta.com/design/48317
http://www.pixelmarta.com/design/2739164/business-card-design-by-frostlynk
http://www.pixelmarta.com/design/604281/business-card-design-by-koralind-vestrabanu

See attachment for my company logo.
Updates

I would like to thank everyone for submitting! I'll need a couple of days to review and ultimately select a design.

Target Market(s)

Non-technical entrepreneurs and small companies.

Industry/Entity Type

University

Requirements
Must have
• My company logo.
In any way, both colors from my logo.
First- and last name, e-mail and phone number.
Double-sided design.
Nice to have
• Something creative with the symbol in my logo

```html
<!DOCTYPE html>
<html lang="en">
<head>
<meta charset="utf-8">
<title>Bexil Software – Business Card</title>
<link rel="stylesheet" href="https://fonts.googleapis.com/css2?family=Questrial&family=Crimson+Pro:wght@400&display=swap">
<style>
  :root {
    --brand-blue: #3d74fb;
    --backdrop: #0e1114;
    --front-core: #1c1f22;
    --front-edge: #0c0e10;
    --back-core: #252d3b;
    --back-edge: #151b23;
    --faint-mark: rgba(58, 84, 140, 0.22);
    --ink-light: #f2f3f5;
  }
  * { margin: 0; padding: 0; box-sizing: border-box; }
  html, body {
    width: 1200px;
    height: 1041px;
    overflow: hidden;
    background: var(--backdrop);
  }
  .sheet {
    position: relative;
    width: 1200px;
    height: 1041px;
    background: var(--backdrop);
  }
  .card {
    position: absolute;
    top: 0;
    width: 555px;
    height: 1041px;
    overflow: hidden;
  }
  .card::before, .card::after {
    content: "";
    position: absolute;
    left: 0;
    width: 100%;
    height: 26px;
    background: var(--brand-blue);
  }
  .card::before { top: 0; }
  .card::after { bottom: 0; }

  .card--front {
    left: 22px;
    background: radial-gradient(circle at 50% 48%, var(--front-core) 0%, #15181b 45%, var(--front-edge) 100%);
  }
  .card--back {
    left: 622px;
    background: radial-gradient(circle at 50% 45%, var(--back-core) 0%, #1c232e 50%, var(--back-edge) 100%);
  }

  .front-mark {
    position: absolute;
    left: 50%;
    top: 510px;
    transform: translate(-50%, -50%);
    display: flex;
    align-items: center;
    gap: 26px;
  }
  .front-mark__dot {
    width: 64px;
    height: 64px;
    border-radius: 50%;
    background: var(--brand-blue);
  }
  .front-mark__name {
    font-family: "Questrial", sans-serif;
    font-size: 112px;
    color: var(--brand-blue);
    line-height: 1;
  }

  .back-logo {
    position: absolute;
    left: 50%;
    top: 146px;
    transform: translate(-50%, -50%);
    display: flex;
    align-items: center;
    gap: 22px;
  }
  .back-logo__dot {
    width: 44px;
    height: 44px;
    border-radius: 50%;
    background: var(--brand-blue);
  }
  .back-logo__name {
    font-family: "Questrial", sans-serif;
    font-size: 92px;
    color: var(--brand-blue);
    line-height: 1;
  }

  .back-watermark {
    position: absolute;
    left: 50%;
    top: 500px;
    width: 440px;
    height: 440px;
    transform: translate(-50%, -50%);
    border-radius: 50%;
    background: var(--faint-mark);
  }

  .holder-name {
    position: absolute;
    left: 0;
    width: 100%;
    top: 806px;
    text-align: center;
    font-family: "Questrial", sans-serif;
    font-size: 62px;
    letter-spacing: 1px;
    color: var(--brand-blue);
    line-height: 1;
  }
  .contact {
    position: absolute;
    left: 0;
    width: 100%;
    top: 924px;
    text-align: center;
    font-family: "Crimson Pro", serif;
    font-size: 30px;
    line-height: 39px;
    color: var(--ink-light);
    list-style: none;
  }
</style>
</head>
<body>
  <main class="sheet">
    <section class="card card--front" aria-label="Card front">
      <div class="front-mark">
        <span class="front-mark__dot" aria-hidden="true"></span>
        <span class="front-mark__name">Bexil</span>
      </div>
    </section>

    <section class="card card--back" aria-label="Card back">
      <div class="back-logo">
        <span class="back-logo__dot" aria-hidden="true"></span>
        <span class="back-logo__name">Bexil</span>
      </div>
      <div class="back-watermark" aria-hidden="true"></div>
      <h1 class="holder-name">Your Name</h1>
      <ul class="contact">
        <li class="contact__phone">+1234567890555</li>
        <li class="contact__email">yourname@postvane.com</li>
      </ul>
    </section>
  </main>
</body>
</html>
```